Business card for marketing analytics company

Need a business card for new company. I have a logo already that I want to be built into the card and should use those colours

Company is called steered by tallies
Design must bring steered by tallies to life not be a card that could be for anyone with a logo put on it.

Like the front to be fairly clean and uncluttered bringing the logo out with a suitable design on the back of the card.

The logo represents a compass and business growth so those themes along with numbers, analytics , data are appropriate.
I'm often working with creative industries so also needs to reflect the creative side of analytics rather than be very corporate looking.

Target Market(s)

Ad agency, media agency, consumer goods clients

Industry/Entity Type

Market Research

Contact Information for Business Card

Needs to include name, title, email and phone number

Colors
f78f20
f68d4d
ec1f27

Requirements
Must have
• Must bring steered by tallies to life not be a card that could be for anyone with a logo put on it.
• Logo, Correct colours
• Like a design on the back that relates to company name
• Designs for both sides
Should not have
• Please do not just submit logo and a coloured card.
• It needs to have a design element to it
• No black background
• No clear cards - needs front & back

```html
<!DOCTYPE html>
<html lang="en">
<head>
<meta charset="utf-8">
<title>Steered by Tallies – Business Card</title>
<link rel="stylesheet" href="https://fonts.googleapis.com/css2?family=Montserrat:wght@600&family=Open+Sans:wght@400;600&display=swap">
<style>
  :root {
    --orange: #f78f20;
    --orange-deep: #f26e22;
    --coral: #f68d4d;
    --red: #ec1f27;
    --white: #ffffff;
    --ink: #1c1c1c;
    --grey: #555a60;
    --icon-grey: #5b6168;
    --rule-grey: #c9c9c9;
    --backdrop: #ecebe8;
  }
  * { margin: 0; padding: 0; box-sizing: border-box; }
  html, body {
    width: 1200px;
    height: 1016px;
    overflow: hidden;
    background: var(--backdrop);
  }
  .canvas {
    position: relative;
    width: 1200px;
    height: 1016px;
  }
  .card {
    position: absolute;
    left: 260px;
    width: 680px;
    height: 440px;
    overflow: hidden;
    background: var(--white);
    box-shadow: 0 6px 18px rgba(0,0,0,0.12);
  }
  .card--front { top: 48px; }
  .card--back  { top: 528px; }

  /* Front */
  .front-band {
    position: absolute;
    inset: 0 0 auto 0;
    height: 132px;
    background: linear-gradient(100deg, var(--orange) 0%, var(--orange-deep) 100%);
  }
  .brand {
    position: absolute;
    display: flex;
    align-items: center;
    gap: 16px;
    color: var(--white);
    font-family: 'Montserrat', sans-serif;
    font-weight: 600;
    line-height: 1.02;
  }
  .brand__dot {
    flex: none;
    border: 3px solid var(--white);
    border-radius: 50%;
  }
  .front-band .brand { left: 40px; top: 28px; font-size: 27px; }
  .front-band .brand__dot { width: 76px; height: 76px; }
  .band-rules {
    position: absolute;
    left: 0; right: 0;
    top: 136px;
    height: 4px;
    background: var(--red);
  }
  .band-rules::after {
    content: "";
    position: absolute;
    left: 0; right: 0;
    top: 7px;
    height: 1px;
    background: var(--rule-grey);
  }
  .person {
    position: absolute;
    left: 44px;
    top: 176px;
    font-family: 'Open Sans', sans-serif;
  }
  .person__name {
    font-size: 27px;
    font-weight: 400;
    color: var(--ink);
  }
  .person__title {
    margin-top: 6px;
    font-size: 15px;
    letter-spacing: 0.5px;
    color: var(--grey);
    text-transform: uppercase;
  }
  .contacts {
    position: absolute;
    left: 36px;
    top: 318px;
    list-style: none;
    font-family: 'Open Sans', sans-serif;
    font-size: 20px;
    color: var(--grey);
  }
  .contacts li {
    display: flex;
    align-items: center;
    gap: 14px;
    height: 40px;
    margin-bottom: 10px;
  }
  .contact-icon {
    width: 34px;
    height: 34px;
    flex: none;
  }

  /* Back */
  .card--back {
    background: linear-gradient(115deg, var(--orange) 0%, var(--orange-deep) 100%);
  }
  .back-watermark {
    position: absolute;
    left: 40px;
    top: 250px;
    font-family: 'Montserrat', sans-serif;
    font-weight: 600;
    font-size: 110px;
    line-height: 0.95;
    color: rgba(255,255,255,0.08);
    white-space: nowrap;
  }
  .card--back .brand { left: 150px; top: 120px; font-size: 48px; }
  .card--back .brand__dot { width: 120px; height: 120px; border-width: 4px; }
  .web-address {
    position: absolute;
    right: 44px;
    bottom: 40px;
    font-family: 'Open Sans', sans-serif;
    font-size: 18px;
    letter-spacing: 0.5px;
    color: var(--white);
  }
</style>
</head>
<body>
<main class="canvas">

  <section class="card card--front" aria-label="Business card front">
    <header class="front-band">
      <div class="brand">
        <span class="brand__dot" aria-hidden="true"></span>
        <span class="brand__name">Steered by<br>Tallies</span>
      </div>
    </header>
    <div class="band-rules" aria-hidden="true"></div>

    <div class="person">
      <p class="person__name">Dan Whitfield</p>
      <p class="person__title">Account Manager</p>
    </div>

    <ul class="contacts">
      <li>
        <svg class="contact-icon" viewBox="0 0 34 34" aria-hidden="true">
          <rect width="34" height="34" rx="7" fill="var(--icon-grey)"/>
          <rect x="11" y="6" width="12" height="22" rx="2.5" fill="none" stroke="var(--white)" stroke-width="2"/>
          <rect x="13.5" y="9" width="7" height="7" fill="var(--white)"/>
          <circle cx="17" cy="23" r="1.6" fill="var(--white)"/>
        </svg>
        <span>0203 555 0187</span>
      </li>
      <li>
        <svg class="contact-icon" viewBox="0 0 34 34" aria-hidden="true">
          <rect width="34" height="34" rx="7" fill="var(--icon-grey)"/>
          <rect x="7" y="10" width="20" height="14" rx="1.5" fill="none" stroke="var(--white)" stroke-width="2"/>
          <path d="M7.5 11 L17 18.5 L26.5 11" fill="none" stroke="var(--white)" stroke-width="2"/>
        </svg>
        <span>danwhitfield@steeredbytallies.com</span>
      </li>
    </ul>
  </section>

  <section class="card card--back" aria-label="Business card back">
    <p class="back-watermark" aria-hidden="true">Steered by<br>Tallies</p>
    <div class="brand">
      <span class="brand__dot" aria-hidden="true"></span>
      <span class="brand__name">Steered by<br>Tallies</span>
    </div>
    <p class="web-address">WWW.STEEREDBYTALLIES.COM</p>
  </section>

</main>
</body>
</html>
```